Brell Stone Company Business Cards

Front and Back Business Card - logo and text setup - cool design. I need workable photoshop or illustrator files so I can setup each employee card with design that is created
Updates

Hi everyone, thank you for the great entries. Please no more white and blue cards - there are so many already - black and silver only now please. thanks!

Target Market(s)

Construction Industry - Facility Managers

Industry/Entity Type

Construction

Contact Information for Business Card

I really like contemporary simplistic looks - clean neat....not opposed to seeing some black backrounds

Requirements
Must have
• Logo/website address with design on front only - www.brellstone-example.com (logo attached)
• Back:
• Name/Title/Company Address/Phone/email address
Nice to have
• Cool design
Should not have
• Nothing gimmicky like Fire or Water - since we are a Fire Protection company - it has all been done

```html
<!DOCTYPE html>
<html lang="en">
<head>
<meta charset="utf-8">
<title>Brell Stone Company Business Cards</title>
<link rel="stylesheet" href="https://fonts.googleapis.com/css2?family=Roboto:wght@400;700&display=swap">
<style>
  :root {
    --page-bg: #e4e4e4;
    --card-white: #ffffff;
    --brand-black: #1f2124;
    --brand-silver: #8c9198;
    --silver-light: #c3c7cc;
    --text-grey: #3f3f3f;
    --rule-grey: #555555;
    --card-black: #1c1d1f;
    --deboss-black: #0e0e0f;
  }
  html, body {
    margin: 0;
    width: 1125px;
    height: 1200px;
    overflow: hidden;
    background: var(--page-bg);
    font-family: "Roboto", Arial, sans-serif;
  }
  .canvas {
    position: relative;
    width: 1125px;
    height: 1200px;
  }
  .card {
    position: absolute;
    left: 156px;
    width: 826px;
    height: 472px;
    overflow: hidden;
  }
  .card-front { top: 106px; background: var(--card-white); }
  .card-back { top: 639px; background: var(--card-black); }

  .company-name {
    position: absolute;
    margin: 0;
    font-weight: 700;
    white-space: nowrap;
  }
  .card-front .company-name {
    right: 48px;
    top: 66px;
    font-size: 58px;
    line-height: 1;
    color: var(--brand-black);
  }
  .card-back .company-name {
    left: 0;
    right: 0;
    top: 192px;
    text-align: center;
    font-size: 84px;
    line-height: 1;
    color: var(--deboss-black);
  }

  .person-name {
    position: absolute;
    left: 46px;
    top: 231px;
    margin: 0;
    font-size: 30px;
    font-weight: 700;
    color: var(--brand-black);
  }
  .person-title {
    position: absolute;
    left: 46px;
    top: 267px;
    margin: 0;
    font-size: 20px;
    font-weight: 400;
    color: var(--brand-silver);
  }
  .divider {
    position: absolute;
    left: 50px;
    top: 314px;
    width: 729px;
    height: 1px;
    background: var(--rule-grey);
  }
  .contact-list {
    position: absolute;
    left: 48px;
    top: 335px;
    margin: 0;
    padding: 0;
    list-style: none;
    font-size: 19px;
    color: var(--text-grey);
  }
  .contact-list li {
    display: flex;
    align-items: center;
    height: 26px;
  }
  .contact-icon {
    width: 18px;
    height: 18px;
    margin-right: 14px;
    fill: var(--brand-black);
  }
  .address {
    position: absolute;
    right: 52px;
    top: 361px;
    margin: 0;
    font-style: normal;
    font-size: 19px;
    line-height: 25px;
    text-align: right;
    color: var(--text-grey);
  }
  .footer-bands {
    position: absolute;
    left: 0;
    top: 0;
    width: 826px;
    height: 472px;
  }
  .website {
    position: absolute;
    right: 8px;
    top: 436px;
    width: 310px;
    margin: 0;
    text-align: center;
    white-space: nowrap;
    font-size: 17px;
    line-height: 24px;
    letter-spacing: 2px;
    color: var(--card-white);
  }
</style>
</head>
<body>
<main class="canvas">

  <section class="card card-front" aria-label="Business card front">
    <svg class="footer-bands" viewBox="0 0 826 472" aria-hidden="true">
      <rect x="0" y="459" width="826" height="13" fill="var(--brand-black)"/>
      <polygon points="0,444 480,444 471,457 0,457" fill="var(--silver-light)"/>
      <polygon points="504,424 826,424 826,472 472,472" fill="var(--card-white)"/>
      <polygon points="508,424 826,424 826,472 478,472" fill="var(--brand-black)"/>
    </svg>

    <h1 class="company-name">Brell Stone</h1>

    <h2 class="person-name">Daniel Reyes</h2>
    <p class="person-title">CEO/Founder</p>
    <div class="divider"></div>

    <ul class="contact-list">
      <li>
        <svg class="contact-icon" viewBox="0 0 24 24" aria-label="Phone"><path d="M6.6 10.8a15.1 15.1 0 0 0 6.6 6.6l2.2-2.2c.3-.3.7-.4 1-.2 1.1.4 2.3.6 3.6.6.6 0 1 .4 1 1V20c0 .6-.4 1-1 1A17 17 0 0 1 3 4c0-.6.4-1 1-1h3.5c.6 0 1 .4 1 1 0 1.3.2 2.5.6 3.6.1.3 0 .7-.2 1z"/></svg>
        (555) 014-2286
      </li>
      <li>
        <svg class="contact-icon" viewBox="0 0 24 24" aria-label="Fax"><path d="M7 2h10v5H7zM3 8h18a1 1 0 0 1 1 1v8h-4v-3H6v3H2V9a1 1 0 0 1 1-1zm4 7h10v7H7z"/></svg>
        (555) 014-2287
      </li>
      <li>
        <svg class="contact-icon" viewBox="0 0 24 24" aria-label="Email"><path d="M2 5h20v14H2zm2 2v.4l8 5.2 8-5.2V7zm0 2.8V17h16V9.8l-8 5.2z"/></svg>
        info@brellstone-example.com
      </li>
    </ul>

    <address class="address">48 Meridian Way<br>Harlow Point, NY 10990</address>

    <p class="website">www.brellstone-example.com</p>
  </section>

  <section class="card card-back" aria-label="Business card back">
    <p class="company-name">Brell Stone</p>
  </section>

</main>
</body>
</html>
```